Business card design and logo for hot water plumbing business

I need a logo and business card for my business which installs hot water heaters
Must have on front:
Bramblefield Hot Water Solutions
Gareth Pennick
0417382946

Either front or back:
gareth@bramblefieldhotwatersolutions.com.au
ABN 48276153094
Licence No 583214K

On the back in point form:
Supply and installation of
• electric storage
• gas storage/instantaneous
• heat pumps
• solar heaters

Iv provided 3 examples of cards I like but open to different ideas.

```html
<!DOCTYPE html>
<html lang="en">
<head>
<meta charset="utf-8">
<title>Bramblefield Hot Water Solutions – Business Card</title>
<link rel="stylesheet" href="https://fonts.googleapis.com/css2?family=Mulish:wght@400;600;700&display=swap">
<style>
  :root {
    --page-bg: #ece9e6;
    --card-light: #f7f7f7;
    --card-mid: #d4d4d4;
    --card-dark: #a9a9a9;
    --band-grey: #3b3a39;
    --band-black: #1c1b1b;
    --band-text: #ffffff;
    --ink: #1f1f1f;
    --brand-ink: #3c3c3c;
    --brand-dot: #4a9fdc;
  }
  * { margin: 0; padding: 0; box-sizing: border-box; }
  html, body {
    width: 1200px; height: 899px; overflow: hidden;
    background: var(--page-bg);
    font-family: "Mulish", "Century Gothic", sans-serif;
    color: var(--ink);
  }
  .canvas { position: relative; width: 1200px; height: 899px; }

  .card {
    position: absolute;
    overflow: hidden;
    box-shadow: 0 10px 24px rgba(0,0,0,0.28);
  }
  .card-backdrop { position: absolute; inset: 0; width: 100%; height: 100%; }

  /* Front */
  .card-front { left: 153px; top: 60px; width: 667px; height: 383px; }
  .front-brand {
    position: absolute; left: 0; right: 0; top: 70px;
    display: flex; flex-direction: column; align-items: center; gap: 14px;
  }
  .brand-dot {
    width: 92px; height: 92px; border-radius: 50%;
    background: var(--brand-dot);
  }
  .brand-name {
    font-weight: 700; color: var(--brand-ink);
    font-size: 20px; letter-spacing: -0.2px; white-space: nowrap;
  }
  .name-band {
    position: absolute; left: 0; right: 0; top: 299px; height: 54px;
    display: flex;
  }
  .name-band .holder {
    flex: 0 0 403px; background: var(--band-grey);
    color: var(--band-text); font-size: 26px;
    display: flex; align-items: center; padding-left: 93px;
  }
  .name-band .phone {
    flex: 1; background: var(--band-black);
    color: var(--band-text); font-size: 29px; letter-spacing: 0.5px;
    display: flex; align-items: center; padding-left: 42px;
  }

  /* Back */
  .card-back { left: 374px; top: 456px; width: 669px; height: 380px; }
  .back-brand {
    position: absolute; left: 34px; top: 20px;
    display: flex; flex-direction: column; align-items: center; gap: 10px;
  }
  .back-brand .brand-dot { width: 66px; height: 66px; }
  .back-brand .brand-name { font-size: 13px; }
  .contact {
    position: absolute; left: 248px; top: 118px;
    font-size: 16.5px; line-height: 21px; color: var(--ink);
  }
  .services {
    position: absolute; left: 42px; top: 226px;
    font-size: 19px; line-height: 25px;
  }
  .services h2 { font-size: 20px; font-weight: 700; line-height: 26px; }
  .services ul { list-style: none; font-weight: 600; }
  .services li::before { content: "\2022"; margin-right: 7px; }
</style>
</head>
<body>
<main class="canvas">

  <section class="card card-front" aria-label="Card front">
    <svg class="card-backdrop" viewBox="0 0 667 383" preserveAspectRatio="none" aria-hidden="true">
      <defs>
        <linearGradient id="frontSheen" x1="0" y1="0" x2="1" y2="1">
          <stop offset="0" stop-color="#ffffff"/>
          <stop offset="0.55" stop-color="#e4e4e4"/>
          <stop offset="1" stop-color="#c6c6c6"/>
        </linearGradient>
        <linearGradient id="frontShade" x1="0" y1="0" x2="1" y2="0">
          <stop offset="0" stop-color="#c2c2c2"/>
          <stop offset="1" stop-color="#dadada"/>
        </linearGradient>
      </defs>
      <rect width="667" height="383" fill="url(#frontSheen)"/>
      <polygon points="300,0 667,0 667,120" fill="#d0d0d0" opacity="0.7"/>
      <polygon points="0,120 667,330 667,383 0,383" fill="url(#frontShade)"/>
    </svg>
    <div class="front-brand">
      <span class="brand-dot" aria-hidden="true"></span>
      <span class="brand-name">Bramblefield Hot Water Solutions</span>
    </div>
    <div class="name-band">
      <span class="holder">Gareth Pennick</span>
      <span class="phone">0417382946</span>
    </div>
  </section>

  <section class="card card-back" aria-label="Card back">
    <svg class="card-backdrop" viewBox="0 0 669 380" preserveAspectRatio="none" aria-hidden="true">
      <defs>
        <linearGradient id="backSheen" x1="0" y1="0" x2="1" y2="1">
          <stop offset="0" stop-color="#ffffff"/>
          <stop offset="0.5" stop-color="#ececec"/>
          <stop offset="1" stop-color="#bdbdbd"/>
        </linearGradient>
      </defs>
      <rect width="669" height="380" fill="url(#backSheen)"/>
      <polygon points="300,0 669,0 669,110" fill="#d2d2d2" opacity="0.75"/>
      <polygon points="0,125 669,345 669,380 0,380" fill="#d8d8d8" opacity="0.8"/>
      <polygon points="330,230 669,150 669,320" fill="#a8a8a8" opacity="0.35"/>
    </svg>
    <div class="back-brand">
      <span class="brand-dot" aria-hidden="true"></span>
      <span class="brand-name">Bramblefield Hot Water Solutions</span>
    </div>
    <address class="contact" style="font-style:normal">
      gareth@bramblefieldhotwatersolutions.com.au<br>
      ABN 48276153094<br>
      Licence No 583214K
    </address>
    <div class="services">
      <h2>Supply and installation of</h2>
      <ul>
        <li>electric storage</li>
        <li>gas storage/instantaneous</li>
        <li>heat pumps</li>
        <li>solar heaters</li>
      </ul>
    </div>
  </section>

</main>
</body>
</html>
```